Marlowe Group needs a business card

I would like the card to be simple but modern and elegant.
I like black and white.
or black and gold.
we are a private finance lender and also are involved in property and property developments.

please look at the business card photos i provided i would like M.G only one one side and all the other details on the other side use fonts that tie in with my theme.

Industry/Entity Type

Finance

Contact Information for Business Card

Marlowe Group (M.G) Daniel Marlowe M: 0413586207 E: danmarl@inboxmail.test

Font styles to use
Other font styles liked:
• Use fonts that would reflect our business

Colors
000000
ffffff

Requirements
Must have
• one side of details
• other side has either M.G or Marlowe Group like in the photos provided

```html
<!DOCTYPE html>
<html lang="en">
<head>
<meta charset="utf-8">
<title>Marlowe Group – Business Card</title>
<link rel="stylesheet" href="https://fonts.googleapis.com/css2?family=Lato:wght@300;400&display=swap">
<style>
  :root {
    --backdrop: #e7e7e9;
    --card-black: #0c0c0c;
    --card-black-soft: #161616;
    --gold-deep: #dc9d12;
    --gold-mid: #f2b91c;
    --gold-bright: #ffd81a;
    --gold-line: #e8b21a;
    --ink-dark: #3a2b05;
  }
  * { box-sizing: border-box; margin: 0; padding: 0; }
  html, body {
    width: 1200px;
    height: 800px;
    overflow: hidden;
    background: var(--backdrop);
    font-family: "Lato", Arial, sans-serif;
  }
  .stage {
    width: 1200px;
    height: 800px;
    display: flex;
    align-items: center;
    justify-content: center;
    gap: 60px;
  }
  .card {
    position: relative;
    width: 520px;
    height: 297px;
    background: radial-gradient(ellipse at 30% 20%, var(--card-black-soft), var(--card-black) 70%);
    box-shadow: 0 10px 24px rgba(0, 0, 0, 0.18);
    overflow: hidden;
  }

  /* Details side */
  .details-frame {
    position: absolute;
    inset: 22px 26px;
    border: 1px solid var(--gold-line);
  }
  .details-panel {
    position: absolute;
    inset: 27px 31px;
    background: linear-gradient(125deg, var(--gold-deep) 0%, var(--gold-mid) 45%, var(--gold-bright) 100%);
    padding: 26px 28px;
    color: var(--ink-dark);
  }
  .company-name {
    font-weight: 300;
    font-size: 19px;
    letter-spacing: 0.06em;
    text-transform: uppercase;
  }
  .contact-list {
    list-style: none;
    margin-top: 44px;
  }
  .contact-item {
    display: inline-block;
    font-weight: 300;
    font-size: 13.5px;
    letter-spacing: 0.02em;
    padding-bottom: 2px;
    border-bottom: 1px solid var(--ink-dark);
    margin-bottom: 8px;
  }
  .contact-list li { display: block; }

  /* Monogram side */
  .monogram-side {
    display: flex;
    align-items: center;
    justify-content: center;
  }
  .monogram {
    color: var(--gold-mid);
    font-weight: 300;
    font-size: 62px;
    letter-spacing: 0.04em;
  }
</style>
</head>
<body>
  <main class="stage">
    <section class="card details-side" aria-label="Business card, details side">
      <div class="details-frame"></div>
      <div class="details-panel">
        <h1 class="company-name">Marlowe Group (M.G)</h1>
        <ul class="contact-list">
          <li><span class="contact-item">Daniel Marlowe</span></li>
          <li><span class="contact-item">0413586207</span></li>
          <li><span class="contact-item">danmarl@inboxmail.test</span></li>
        </ul>
      </div>
    </section>

    <section class="card monogram-side" aria-label="Business card, monogram side">
      <p class="monogram">M.G</p>
    </section>
  </main>
</body>
</html>
```